Home Remodeler Needs a Website!

Single page (plus contact form) website for small home remodeling company. He's got a few pictures he'd like on the site and needs some basic text. He likes clean, simple designs and is "more traditional" in his stylistic preferences. Most of his business comes from word-of-mouth advertising and so the site is just something he needs for people to feel more comfortable with his business.

Target Market(s)

People who want to remodel their homes

Coding

Coded - Design and coding required

Number of Pages Required

2 page

Requirements
Must have
• Main page to include some or all of the attached images, contact page. Neutral colors. Old domain: lindcroftmeadowbuild.com New domain: qm-ventureworks.com You can pull text from the old site or update it.
Should not have
• No loud colors/loud visual elements

```html
<!DOCTYPE html>
<html lang="en">
<head>
<meta charset="utf-8">
<title>Lindcroft Meadow Homes</title>
<link href="https://fonts.googleapis.com/css2?family=Cinzel:wght@400;700&family=Mulish:wght@400;600;700;800&display=swap" rel="stylesheet">
<style>
:root{
  --navy:#0a0a96;
  --orange:#ee4a1f;
  --ink:#1a1a1a;
  --muted:#666;
  --lilac:#f0f0fa;
  --white:#fff;
  --line:#d4d4dc;
}
*{margin:0;padding:0;box-sizing:border-box}
html,body{width:1200px;height:3666px;overflow:hidden}
body{position:relative;font-family:"Mulish",sans-serif;color:var(--ink);background:var(--white)}
.abs{position:absolute}
.serif{font-family:"Cinzel",serif}

.topbar{left:0;top:0;width:1200px;height:80px;background:var(--navy)}
.brand{left:147px;top:10px;color:var(--white)}
.brand-name{font-family:"Cinzel",serif;font-size:32px;line-height:36px;font-weight:400}
.brand-sub{font-size:13px;font-weight:700;margin-top:2px}
.nav{left:431px;top:0;height:80px;display:flex;align-items:center}
.nav a{color:var(--white);text-decoration:none;font-size:13.5px;font-weight:700;padding:0 15px;height:80px;line-height:80px}
.nav a.active{background:var(--orange);padding:0 21px}
.search{left:1041px;top:32px}

.hero{left:0;top:80px;width:1200px;height:615px;background:linear-gradient(120deg,#2a2320 0%,#4a3a2e 40%,#231c18 70%,#3a2e26 100%)}
.hero-title{left:0;top:220px;width:1200px;text-align:center;color:var(--white);font-family:"Cinzel",serif;font-size:128px;line-height:130px;text-shadow:0 3px 8px rgba(0,0,0,.5)}
.hero-sub{left:0;top:385px;width:1200px;text-align:center;color:var(--white);font-size:50px;font-weight:600;text-shadow:0 3px 8px rgba(0,0,0,.5)}
.btn{display:block;background:var(--orange);color:var(--white);text-align:center;font-weight:600;border-radius:30px;text-decoration:none}
.hero-btn{left:504px;top:484px;width:192px;height:58px;line-height:58px;font-size:17px}
.dots{left:563px;top:621px;display:flex;gap:8px}
.dots span{width:8px;height:8px;border-radius:50%;background:var(--white)}
.dots span.on{background:#f2a23a}

.photo-band{left:0;top:1073px;width:1200px;height:577px;background:linear-gradient(180deg,#6f6a5e 0%,#5b5144 55%,#3d3026 100%)}
.welcome{left:144px;top:680px;width:911px;height:526px;background:var(--white);text-align:center}
.welcome h2{font-family:"Cinzel",serif;font-weight:400;color:var(--navy);font-size:58px;margin-top:80px;line-height:64px}
.welcome h3{font-family:"Cinzel",serif;font-weight:400;color:var(--ink);font-size:42px;line-height:50px;margin-top:2px}
.welcome p{width:810px;margin:38px auto 0;font-size:15.5px;line-height:28px;color:var(--muted)}
.read-btn{position:absolute;left:360px;top:383px;width:192px;height:59px;line-height:59px;font-size:17px}

.navy-block{left:0;top:1650px;width:463px;height:632px;background:var(--navy)}
.kitchen-photo{left:67px;top:1724px;width:535px;height:632px;background:linear-gradient(135deg,#214f8a 0%,#6d6f70 45%,#8a8c8c 60%,#5a3c26 100%)}
.offer{left:673px;top:1780px;width:480px}
.offer h2{font-family:"Cinzel",serif;font-weight:400;font-size:43px;line-height:48px;color:var(--ink)}
.offer h2 .blue{color:var(--navy)}
.offer .tag{font-size:25px;font-weight:600;margin-top:22px;color:#222}
.offer ul{list-style:none;margin-top:20px}
.offer li{font-size:15.5px;color:var(--muted);height:36px;line-height:36px;display:flex;align-items:center}
.offer li svg{margin:0 19px 0 7px}

.services{left:0;top:2356px;width:1200px;height:517px;background:var(--lilac)}
.section-title{font-family:"Cinzel",serif;font-weight:400;font-size:44px;text-align:center;width:1200px;left:0;color:var(--ink)}
.section-title .blue{color:var(--navy)}
.svc{width:240px;text-align:center;top:2553px}
.svc-ring{width:166px;height:166px;border:7px solid var(--orange);border-radius:50%;margin:0 auto;display:flex;align-items:center;justify-content:center;background:var(--white)}
.svc-label{font-size:16px;font-weight:600;line-height:22px;margin-top:20px}

.field{border:1px solid var(--line);background:var(--white);font-size:15.5px;color:#444;padding:0 21px;line-height:54px}
.submit{left:488px;top:3345px;width:224px;height:58px;line-height:58px;font-size:17px}

.footer{left:0;top:3490px;width:1200px;height:176px;background:var(--navy);color:var(--white)}
.fnav{left:149px;top:3522px;display:flex;gap:29px;font-size:13px;font-weight:700}
.copy{left:149px;top:3562px;font-size:12px}
.social{left:149px;top:3605px;display:flex;gap:16px}
.social span{width:20px;height:20px;border-radius:50%;background:var(--white)}
.phones{left:850px;top:3517px;font-size:29px;font-weight:800;line-height:36px}
.phone-ic{left:787px;top:3528px}
</style>
</head>
<body>

<header class="abs topbar"></header>
<div class="abs brand">
  <div class="brand-name">Lindcroft</div>
  <div class="brand-sub">MEADOW HOMES</div>
</div>
<nav class="abs nav">
  <a class="active" href="#">HOME</a>
  <a href="#">ABOUT US</a>
  <a href="#">PRODUCTS</a>
  <a href="#">EXTRAS</a>
  <a href="#">RESOURCES</a>
  <a href="#">CONTACT US</a>
</nav>
<svg class="abs search" width="16" height="16" viewBox="0 0 16 16"><circle cx="6.5" cy="6.5" r="4.5" fill="none" stroke="#fff" stroke-width="2"/><line x1="10" y1="10" x2="14" y2="14" stroke="#fff" stroke-width="2.4"/></svg>

<section class="abs hero" role="img" aria-label="Dim remodeled kitchen with dark wood cabinets, stone wall and wine rack"></section>
<div class="abs hero-title">Lindcroft</div>
<div class="abs hero-sub">MEADOW HOMES</div>
<a class="abs btn hero-btn" href="#">GET STARTED</a>
<div class="abs dots"><span></span><span></span><span class="on"></span><span></span><span></span></div>

<div class="abs photo-band" role="img" aria-label="Open finished basement with kitchenette, bar stools and French doors"></div>
<section class="abs welcome">
  <h2>Welcome to</h2>
  <h3>Lindcroft Meadow Homes</h3>
  <p>When you want affordable, quality home construction services; think of us to do the job.Since 1981 Walter Pryce has built and remodeled over 400 homes and businesses. Let us be your contractor for the next project you start.When quality, value and personal attention to detail are important With over 20 years experience in residential and commercial construction, you can trust your project to Lindcroft Meadow Homes.</p>
  <a class="btn read-btn" href="#">READ MORE</a>
</section>

<div class="abs navy-block"></div>
<div class="abs kitchen-photo" role="img" aria-label="Remodeled kitchen with blue wall, stainless refrigerator and green island"></div>
<section class="abs offer">
  <h2>Commercial and <span class="blue">Residential</span> Contracting</h2>
  <div class="tag">"ALL IN ONE PACKAGE"</div>
  <ul>
    <li><svg width="14" height="14" viewBox="0 0 14 14"><circle cx="7" cy="7" r="5.8" fill="none" stroke="#ee4a1f" stroke-width="1.6"/><path d="M4.3 7.2l2 2 3.5-4" fill="none" stroke="#ee4a1f" stroke-width="1.6"/></svg>Pre Construction Consultation</li>
    <li><svg width="14" height="14" viewBox="0 0 14 14"><circle cx="7" cy="7" r="5.8" fill="none" stroke="#ee4a1f" stroke-width="1.6"/><path d="M4.3 7.2l2 2 3.5-4" fill="none" stroke="#ee4a1f" stroke-width="1.6"/></svg>New Construction</li>
    <li><svg width="14" height="14" viewBox="0 0 14 14"><circle cx="7" cy="7" r="5.8" fill="none" stroke="#ee4a1f" stroke-width="1.6"/><path d="M4.3 7.2l2 2 3.5-4" fill="none" stroke="#ee4a1f" stroke-width="1.6"/></svg>Remodeling / kitchens and baths</li>
    <li><svg width="14" height="14" viewBox="0 0 14 14"><circle cx="7" cy="7" r="5.8" fill="none" stroke="#ee4a1f" stroke-width="1.6"/><path d="M4.3 7.2l2 2 3.5-4" fill="none" stroke="#ee4a1f" stroke-width="1.6"/></svg>Additions</li>
    <li><svg width="14" height="14" viewBox="0 0 14 14"><circle cx="7" cy="7" r="5.8" fill="none" stroke="#ee4a1f" stroke-width="1.6"/><path d="M4.3 7.2l2 2 3.5-4" fill="none" stroke="#ee4a1f" stroke-width="1.6"/></svg>Porches and Decks</li>
    <li><svg width="14" height="14" viewBox="0 0 14 14"><circle cx="7" cy="7" r="5.8" fill="none" stroke="#ee4a1f" stroke-width="1.6"/><path d="M4.3 7.2l2 2 3.5-4" fill="none" stroke="#ee4a1f" stroke-width="1.6"/></svg>Specializing in historic renovations.</li>
  </ul>
</section>

<section class="abs services"></section>
<h2 class="abs section-title" style="top:2440px">Our <span class="blue">Services</span></h2>
<svg class="abs" style="left:92px;top:2604px" width="34" height="66" viewBox="0 0 34 66"><path d="M32 2L2 33l30 31" fill="none" stroke="#b8b8c8" stroke-width="2"/></svg>
<svg class="abs" style="left:1075px;top:2604px" width="34" height="66" viewBox="0 0 34 66"><path d="M2 2l30 31L2 64" fill="none" stroke="#b8b8c8" stroke-width="2"/></svg>

<div class="abs svc" style="left:125px">
  <div class="svc-ring"><svg width="70" height="60" viewBox="0 0 70 60" fill="none" stroke="#0a0a96" stroke-width="2.5"><path d="M4 14h62v40H4z"/><path d="M4 24h62M4 34h62M4 44h62M20 14v40M36 14v40M52 14v40"/><path d="M44 14V4h10v10"/></svg></div>
  <div class="svc-label">ROOFING</div>
</div>
<div class="abs svc" style="left:361px">
  <div class="svc-ring"><svg width="60" height="66" viewBox="0 0 60 66" fill="none" stroke="#0a0a96" stroke-width="2.5"><rect x="6" y="4" width="48" height="58"/><path d="M12 10h36v22H12zM12 40h36M12 48h36v8H12z"/><path d="M14 30l32-18"/></svg></div>
  <div class="svc-label">WINDOW<br>REPLACEMENT</div>
</div>
<div class="abs svc" style="left:599px">
  <div class="svc-ring"><svg width="66" height="66" viewBox="0 0 66 66" fill="none" stroke="#0a0a96" stroke-width="2.5"><circle cx="33" cy="33" r="30" stroke-dasharray="150 40"/><path d="M25 12v10M41 12v10M20 22h26v10a13 13 0 0 1-26 0z"/><path d="M35 26l-4 7h5l-4 7"/><path d="M33 45v8"/></svg></div>
  <div class="svc-label">ELECTRICAL</div>
</div>
<div class="abs svc" style="left:835px">
  <div class="svc-ring"><svg width="76" height="60" viewBox="0 0 76 60" fill="none" stroke="#0a0a96" stroke-width="2.5"><rect x="4" y="6" width="68" height="26" rx="3"/><path d="M10 24h56M10 28h56M54 13h10"/><path d="M28 38c-3 4 3 8 0 12M38 38c-3 4 3 8 0 12M48 38c-3 4 3 8 0 12"/></svg></div>
  <div class="svc-label">AIR CONDITIONING<br>&amp; PLUMBING</div>
</div>

<h2 class="abs section-title" style="top:2968px">Contact <span class="blue">Us</span></h2>
<div class="abs field" style="left:233px;top:3070px;width:362px;height:55px">First Name</div>
<div class="abs field" style="left:605px;top:3070px;width:361px;height:55px">Last Name</div>
<div class="abs field" style="left:233px;top:3135px;width:362px;height:55px">Email address</div>
<div class="abs field" style="left:605px;top:3135px;width:361px;height:55px">Phone Number</div>
<div class="abs field" style="left:233px;top:3200px;width:733px;height:116px;line-height:20px;padding-top:16px">Message</div>
<a class="abs btn submit" href="#">SUBMIT MESSAGE</a>

<footer class="abs footer"></footer>
<div class="abs fnav" style="color:#fff"><span>HOME</span><span>ABOUT US</span><span>PRODUCTS</span><span>EXTRAS</span><span>RESOURCES</span><span>CONTACT US</span></div>
<div class="abs copy" style="color:#fff">© 2021 Lindcroft Meadow Homes.Al Rights Reserved &nbsp;|&nbsp; Privacy Policy &nbsp;|&nbsp; Terms and use</div>
<div class="abs social"><span></span><span></span><span></span></div>
<svg class="abs phone-ic" width="44" height="44" viewBox="0 0 44 44"><circle cx="22" cy="22" r="20" fill="none" stroke="#ee4a1f" stroke-width="2.5"/><path d="M15 12c-3 2-3 6 0 11s8 9 12 9c2 0 3-1 4-3l-4-4-3 2c-2-1-5-4-6-6l2-3-4-5z" fill="#ee4a1f"/></svg>
<div class="abs phones" style="color:#fff">555-014-2210<br>555-014-7395</div>

</body>
</html>
```